Business Card Design (NEW FILES)

ATTENTION: New vector files are available. Please update your design to reflect/use the new (better resolution) logo images.

Seeking a unique and professional business card design for a commercial drone photography/videography business. The layout should feature
the logo (attached) and include the following information:
Owen Tarrick
614-502-7738
www.skylarkreelworks.example
NRD Certified Remote Pilot

Owen Tarrick

```html
<!DOCTYPE html>
<html lang="en">
<head>
<meta charset="utf-8">
<title>Skylark Reelworks – Business Card</title>
<link rel="stylesheet" href="https://fonts.googleapis.com/css2?family=Lato:wght@400;700;900&display=swap">
<style>
  :root {
    --backdrop: #8f8f8f;
    --navy: #131a46;
    --orange: #ec8a4f;
    --white: #ffffff;
    --ink-grey: #4a4a4a;
  }
  * { margin: 0; padding: 0; box-sizing: border-box; }
  html, body { width: 1200px; height: 1200px; overflow: hidden; }
  body {
    background: var(--backdrop);
    font-family: "Lato", sans-serif;
    position: relative;
  }
  .card {
    position: absolute;
    left: 281px;
    width: 642px;
    height: 366px;
    border-radius: 18px;
    overflow: hidden;
  }
  .card--front { top: 195px; background: var(--white); }
  .card--back { top: 639px; background: var(--navy); }

  .brand {
    position: absolute;
    display: flex;
    align-items: center;
    gap: 10px;
    font-weight: 400;
    letter-spacing: 1px;
    line-height: 1;
    white-space: nowrap;
  }
  .brand__dot { border-radius: 50%; flex: none; }

  .card--front .brand { left: 326px; top: 90px; color: var(--navy); font-size: 25px; }
  .card--front .brand__dot { width: 16px; height: 16px; background: var(--orange); }

  .holder__name {
    position: absolute; left: 38px; top: 186px;
    font-size: 27px; font-weight: 900; color: var(--navy); letter-spacing: 0.3px;
  }
  .holder__role {
    position: absolute; left: 38px; top: 220px;
    font-size: 16px; color: var(--orange);
  }
  .divider {
    position: absolute; left: 38px; top: 250px; width: 563px; height: 1px;
    background: var(--navy);
  }
  .contact { position: absolute; left: 38px; top: 266px; list-style: none; }
  .contact__item {
    display: flex; align-items: center; gap: 10px;
    font-size: 15.5px; color: var(--ink-grey); letter-spacing: 0.4px;
    height: 24px;
  }
  .contact__icon { width: 11px; height: 11px; fill: var(--navy); flex: none; }
  .credential {
    position: absolute; right: 41px; top: 264px;
    font-size: 17px; font-weight: 700; color: var(--navy);
  }
  .footer-bands { position: absolute; left: 0; bottom: 0; width: 642px; height: 32px; }
  .insured {
    position: absolute; right: 60px; bottom: 6px;
    font-size: 16px; font-weight: 900; color: var(--orange); letter-spacing: 0.8px;
  }

  .card--back .brand { left: 130px; top: 148px; color: var(--white); font-size: 36px; }
  .card--back .brand__dot { width: 22px; height: 22px; background: var(--orange); }
</style>
</head>
<body>

  <section class="card card--front" aria-label="Business card, front">
    <div class="brand">
      <span>SKYLARK REELWORKS</span>
      <span class="brand__dot"></span>
    </div>

    <h1 class="holder__name">OWEN TARRICK</h1>
    <p class="holder__role">Owner</p>
    <div class="divider"></div>

    <ul class="contact">
      <li class="contact__item">
        <svg class="contact__icon" viewBox="0 0 24 24" aria-hidden="true"><path d="M6.6 10.8a15.1 15.1 0 0 0 6.6 6.6l2.2-2.2c.3-.3.7-.4 1-.2 1.1.4 2.3.6 3.6.6.6 0 1 .4 1 1V20c0 .6-.4 1-1 1A17 17 0 0 1 3 4c0-.6.4-1 1-1h3.5c.6 0 1 .4 1 1 0 1.3.2 2.5.6 3.6.1.3 0 .7-.2 1z"/></svg>
        614-502-7738
      </li>
      <li class="contact__item">
        <svg class="contact__icon" viewBox="0 0 24 24" aria-hidden="true"><circle cx="12" cy="12" r="11"/><path d="M7 6c2 1 3 3 2 5s1 3 3 3 2 3 1 6M15 3c-1 2 0 4 2 4s3 2 4 4" stroke="#fff" stroke-width="1.8" fill="none"/></svg>
        www.skylarkreelworks.example
      </li>
    </ul>

    <p class="credential">NRD Certified Remote Pilot</p>

    <svg class="footer-bands" viewBox="0 0 642 32" aria-hidden="true">
      <rect x="0" y="8" width="383" height="2" fill="var(--navy)"/>
      <polygon points="0,16 376,16 362,32 0,32" fill="var(--orange)"/>
      <polygon points="393,0 642,0 642,32 368,32" fill="var(--navy)"/>
    </svg>
    <span class="insured">FULLY INSURED</span>
  </section>

  <section class="card card--back" aria-label="Business card, back">
    <div class="brand">
      <span>SKYLARK REELWORKS</span>
      <span class="brand__dot"></span>
    </div>
  </section>

</body>
</html>
```